Velundra Jobs portal

Velundra Jobs is a job portal connecting job seekers and companies offering part time jobs in the Mena region, starting in the UAE. We would like to see designs that use the color blue. We have attached images to give an idea what the website should look like. When a company posts a job the job seekers are not allowed to see which company has posted a job. There should also be a coinvex gateway. On the landing page we want a catching picture that we will send.

Target Market(s)

Students and promotional workers

Logo Text

Velundra Jobs

Coding

Coded - Design and coding required

Number of Pages Required

4 page

Font styles to use
Sans Serif

Colors
33a6d7
0692cd
85cae6

```html
<!DOCTYPE html>
<html lang="en">
<head>
<meta charset="utf-8">
<title>Velundra Jobs – Job Seeker</title>
<link rel="stylesheet" href="https://fonts.googleapis.com/css2?family=Didact+Gothic&family=Open+Sans:wght@400;600&display=swap">
<style>
:root{
  --blue:#33a6d7;
  --blue-deep:#0692cd;
  --blue-soft:#85cae6;
  --pink:#e24a8d;
  --teal:#4dbfc4;
  --teal-line:#5ccbd0;
  --ink:#555;
  --ink-soft:#888;
  --paper:#f7f7f7;
  --footer:#333;
  --footer-base:#2c2c2c;
  --rule:#e3e3e3;
}
*{box-sizing:border-box;margin:0;padding:0}
html,body{width:1070px;height:1200px;overflow:hidden}
body{position:relative;font-family:"Didact Gothic",sans-serif;color:var(--ink);background:#fff}
.abs{position:absolute}

/* header */
.topline{left:0;top:0;width:1070px;height:2px;background:linear-gradient(90deg,var(--blue) 0 25%,#3c6fb8 25% 50%,#8e4aa8 50% 75%,var(--blue-soft) 75%)}
.site-header{left:0;top:2px;width:1070px;height:70px;background:#f6f6f6;border-bottom:1px solid #ddd}
.brand{left:88px;top:20px;font-size:25px;color:var(--blue);line-height:30px}
.nav{left:242px;top:32px;font-size:12px;color:#666;display:flex;gap:28px}
.hdr-cell{top:0;height:70px;border-left:1px solid #e0e0e0}
.icon-search{left:588px;top:22px}
.icon-bell{left:652px;top:20px}
.badge{left:667px;top:17px;width:15px;height:15px;border-radius:50%;background:var(--pink);color:#fff;font:600 8px/15px "Open Sans",sans-serif;text-align:center}
.avatar{left:714px;top:17px;width:39px;height:39px;border-radius:50%;background:radial-gradient(circle at 50% 40%,#b98762,#5a3a26)}
.user{left:767px;top:20px;font-size:10.5px;color:#888;line-height:16px}
.user b{font-weight:400;color:var(--pink)}
.login{left:898px;top:20px;width:83px;height:34px;background:var(--pink);color:#fff;font-size:15px;line-height:34px;text-align:center;border-radius:2px}

/* hero */
.hero{left:0;top:72px;width:1070px;height:157px;background:linear-gradient(100deg,#5db6e0 0%,#3fa6d8 45%,#2e8fc8 100%)}
.hero h1{position:absolute;left:91px;top:17px;font-weight:400;font-size:22px;color:#fff}
.hero p{position:absolute;left:88px;top:54px;font-size:12.5px;color:#fff}
.field{top:94px;height:32px;border:1px solid rgba(255,255,255,.85);color:#fff;font-size:11.5px;line-height:30px;padding-left:10px}
.filter{left:827px;top:91px;width:140px;height:39px;background:#2a8cc4;color:#fff;font:600 12px/39px "Open Sans",sans-serif;text-align:center}

/* listing */
.listing{left:0;top:229px;width:1070px;height:462px;background:var(--paper);border-bottom:1px solid #e8e8e8}
.categories{left:88px;top:28px;width:236px;height:395px;background:var(--teal);border-bottom:3px solid #3aa9ae;list-style:none;padding-top:1px}
.categories li{height:32px;border-bottom:1px solid var(--teal-line);display:flex;justify-content:space-between;padding:0 27px 0 17px;align-items:center;color:#fff;font-size:11.5px}
.jobs{left:359px;top:30px;width:623px;border-collapse:collapse;background:#fff;border:1px solid var(--rule);font-family:"Open Sans",sans-serif}
.jobs th{background:var(--pink);color:#fff;font-weight:400;font-size:13px;text-align:left;height:43px;padding-left:17px;border-right:1px solid #ea73a6}
.jobs td{height:50.7px;font-size:11.5px;color:var(--ink-soft);padding-left:16px;border-right:1px solid var(--rule);border-top:1px solid var(--rule)}
.jobs tr:nth-child(odd) td{background:#f3f3f3}
.jobs tr:first-child td{background:#fff}
.apply{display:inline-block;width:99px;height:31px;background:var(--blue);border-bottom:2px solid #1f80b5;color:#fff;font-size:12px;font-weight:600;text-align:center;line-height:30px;margin-left:10px;border-radius:2px}

/* featured */
.featured-title{left:88px;top:715px;font-size:15.5px;color:#555}
.arrows{left:958px;top:715px;font-size:12px;color:#aaa;letter-spacing:8px}
.card{top:753px;width:212px;height:228px;background:#fff;border:1px solid #ececec;box-shadow:0 1px 2px rgba(0,0,0,.06);text-align:center}
.card .photo{margin:3px 3px 0;height:157px}
.card h3{font-weight:400;font-size:12.5px;color:#555;margin-top:18px}
.card a{display:block;font-size:10.5px;color:var(--blue);text-decoration:none;margin-top:8px}

/* footer */
.site-footer{left:0;top:1010px;width:1070px;height:140px;background:var(--footer);color:#ddd}
.site-footer h4{position:absolute;top:28px;font:400 14.5px "Open Sans",sans-serif;letter-spacing:.5px;color:#eee}
.site-footer .txt{position:absolute;top:60px;font-size:11.5px;line-height:18px;color:#ddd}
.email{left:509px;top:58px;width:189px;height:35px;background:#fff;color:#777;font-size:11.5px;line-height:35px;padding-left:12px}
.subscribe{left:705px;top:58px;width:81px;height:36px;background:var(--blue);border-bottom:2px solid #1f80b5;color:#fff;font:600 11.5px/34px "Open Sans",sans-serif;text-align:center}
.social{left:884px;top:63px}
.base{left:0;top:1150px;width:1070px;height:50px;background:var(--footer-base);border-top:1px solid #3a3a3a;color:#ddd;font-size:11.5px;text-align:center;line-height:46px}
</style>
</head>
<body>
<div class="abs topline"></div>
<header class="abs site-header">
  <div class="abs brand">Velundra Jobs</div>
  <nav class="abs nav"><span>ABOUT US</span><span>CONTACT US</span></nav>
  <div class="abs hdr-cell" style="left:570px"></div>
  <div class="abs hdr-cell" style="left:632px"></div>
  <div class="abs hdr-cell" style="left:698px"></div>
  <div class="abs hdr-cell" style="left:885px"></div>
  <svg class="abs icon-search" width="24" height="24" viewBox="0 0 24 24" aria-label="Search"><circle cx="10" cy="10" r="7" fill="none" stroke="#999" stroke-width="3"/><line x1="15" y1="15" x2="22" y2="22" stroke="#999" stroke-width="3.5" stroke-linecap="round"/></svg>
  <svg class="abs icon-bell" width="24" height="26" viewBox="0 0 24 26" aria-label="Notifications"><path d="M12 3c-4 0-7 3-7 7v6l-2 3h18l-2-3v-6c0-4-3-7-7-7z" fill="none" stroke="#999" stroke-width="2"/><path d="M9 21a3 3 0 0 0 6 0" fill="none" stroke="#999" stroke-width="2"/></svg>
  <div class="abs badge">23</div>
  <div class="abs avatar" role="img" aria-label="User portrait"></div>
  <div class="abs user">NAME : <b>DUMMY NAME</b><br>Posed on 25 March 2015</div>
  <div class="abs login">LOGIN</div>
</header>

<section class="abs hero" role="img" aria-label="Blue-toned photo of hands on a keyboard">
  <h1>Job Seeker</h1>
  <p>It is a long established fact that a reader will be distracted by the readable content of a page when looking at its layout.</p>
  <div class="abs field" style="left:88px;width:159px">Keyword* :</div>
  <div class="abs field" style="left:271px;width:159px">District 1* :</div>
  <div class="abs field" style="left:454px;width:159px">Job* :</div>
  <div class="abs field" style="left:636px;width:172px">Languages Spoken* :</div>
  <div class="abs filter">FILTER JOBS</div>
</section>

<main class="abs listing">
  <ul class="abs categories">
    <li><span>CATEGORY1</span><span>(33)</span></li><li><span>CATEGORY1</span><span>(33)</span></li>
    <li><span>CATEGORY1</span><span>(33)</span></li><li><span>CATEGORY1</span><span>(33)</span></li>
    <li><span>CATEGORY1</span><span>(33)</span></li><li><span>CATEGORY1</span><span>(33)</span></li>
    <li><span>CATEGORY1</span><span>(33)</span></li><li><span>CATEGORY1</span><span>(33)</span></li>
    <li><span>CATEGORY1</span><span>(33)</span></li><li><span>CATEGORY1</span><span>(33)</span></li>
    <li><span>CATEGORY1</span><span>(33)</span></li><li><span>CATEGORY1</span><span>(33)</span></li>
  </ul>
  <table class="abs jobs">
    <thead><tr><th style="width:184px">Job Tittle</th><th style="width:172px">Due Date</th><th style="width:120px">Provider Name</th><th></th></tr></thead>
    <tbody>
      <tr><td>Job TittleNumber 1</td><td>Due date : 23 Mar 2015</td><td>Provider 1</td><td><span class="apply">APPLY NOW!</span></td></tr>
      <tr><td>Job TittleNumber 1</td><td>Due date : 23 Mar 2015</td><td>Provider 1</td><td><span class="apply">APPLY NOW!</span></td></tr>
      <tr><td>Job TittleNumber 1</td><td>Due date : 23 Mar 2015</td><td>Provider 1</td><td><span class="apply">APPLY NOW!</span></td></tr>
      <tr><td>Job TittleNumber 1</td><td>Due date : 23 Mar 2015</td><td>Provider 1</td><td><span class="apply">APPLY NOW!</span></td></tr>
      <tr><td>Job TittleNumber 1</td><td>Due date : 23 Mar 2015</td><td>Provider 1</td><td><span class="apply">APPLY NOW!</span></td></tr>
      <tr><td>Job TittleNumber 1</td><td>Due date : 23 Mar 2015</td><td>Provider 1</td><td><span class="apply">APPLY NOW!</span></td></tr>
      <tr><td>Job TittleNumber 1</td><td>Due date : 23 Mar 2015</td><td>Provider 1</td><td><span class="apply">APPLY NOW!</span></td></tr>
    </tbody>
  </table>
</main>

<h2 class="abs featured-title" style="font-weight:400">FEATURED JOB PROVIDERS</h2>
<div class="abs arrows">‹ ›</div>
<article class="abs card" style="left:88px"><div class="photo" role="img" aria-label="Photo of job candidates waiting in a row" style="background:linear-gradient(180deg,#e8eaec,#c9c6c2)"></div><h3>NEQUE PORRO QUISQUAM</h3><a>Click Here For More Info »</a></article>
<article class="abs card" style="left:315px"><div class="photo" role="img" aria-label="Photo of two colleagues working at a laptop" style="background:linear-gradient(180deg,#eef1f4,#b7bcc2)"></div><h3>NEQUE PORRO QUISQUAM</h3><a>Click Here For More Info »</a></article>
<article class="abs card" style="left:543px"><div class="photo" role="img" aria-label="Photo of a team applauding in a meeting" style="background:linear-gradient(180deg,#e4e9ee,#a9b4c0)"></div><h3>NEQUE PORRO QUISQUAM</h3><a>Click Here For More Info »</a></article>
<article class="abs card" style="left:769px"><div class="photo" role="img" aria-label="Photo of a pen on a job opportunities listing" style="background:linear-gradient(135deg,#1f3a5c,#6f88a8 60%,#c3ccd8)"></div><h3>NEQUE PORRO QUISQUAM</h3><a>Click Here For More Info »</a></article>

<footer class="abs site-footer">
  <h4 style="left:90px">CONTACT US</h4>
  <div class="txt" style="left:88px">42 Harbour Lane, Lorem Ipsum&nbsp; 1400<br>lorem Ipsum&nbsp; 60310-1180</div>
  <div class="txt" style="left:316px">(000)-555-0148<br>help@velundrajobs.ae</div>
  <h4 style="left:510px">NEWSLETTER</h4>
  <div class="abs email">Email:</div>
  <div class="abs subscribe">SUBSCRIBE</div>
  <h4 style="left:884px">FOLLOW US</h4>
  <svg class="abs social" width="100" height="32" viewBox="0 0 100 32" role="img" aria-label="Social links">
    <circle cx="16" cy="16" r="14.5" fill="none" stroke="#eee" stroke-width="2"/>
    <circle cx="49" cy="16" r="14.5" fill="none" stroke="#eee" stroke-width="2"/>
    <circle cx="82" cy="16" r="14.5" fill="none" stroke="#eee" stroke-width="2"/>
  </svg>
</footer>
<div class="abs base">Copyright © 2015 Velundra. all rights are reserved</div>
</body>
</html>
```